Business Card for a mobile physiotherapy company

I need a layout for a business card for a mobile physiotherapy company.
Slogan is "Mobile Physiotherapy - Your Road To Recovery"
Phone number is 867-555-0142
Email VardenTherapy@postnest.ca (subject to change with website)
Website www.VardenTherapy.ca
My name and credentials: Luke Varden Luke Varden, BSc(kin), MPT, CAFCI, IMS
Information maybe included: Direct Billing, Services including Physiotherapy, IMS, acupuncture
Maybe include facebook and instagram logos
One side with the logo clean and sharp
Other side with details, try not to look too busy, keep everything concise

```html
<!DOCTYPE html>
<html lang="en">
<head>
<meta charset="utf-8">
<title>Varden Therapy – Business Card</title>
<link rel="stylesheet" href="https://fonts.googleapis.com/css2?family=Lora:wght@400;600&display=swap">
<style>
  :root {
    --backdrop: #3b3b3d;
    --card: #1e1e20;
    --card-front: #19191b;
    --blue: #1f5585;
    --green: #2f7a57;
    --text-light: #e6e6e6;
    --text-muted: #b8b8b8;
    --front-mark: #8a8a8e;
  }
  * { margin: 0; padding: 0; box-sizing: border-box; }
  html, body { width: 799px; height: 1200px; overflow: hidden; }
  body {
    background: var(--backdrop);
    font-family: "Lora", Georgia, serif;
    display: flex;
    flex-direction: column;
    align-items: center;
    justify-content: space-around;
    padding: 90px 0;
  }
  .card {
    position: relative;
    width: 620px;
    height: 354px;
    border-radius: 18px;
    overflow: hidden;
  }
  .card-front {
    background: var(--card-front);
    display: flex;
    align-items: center;
    justify-content: center;
  }
  .brand-name {
    font-family: "Lora", Georgia, serif;
    font-weight: 600;
    text-transform: uppercase;
    letter-spacing: 6px;
    line-height: 1.05;
    text-align: center;
  }
  .card-front .brand-name {
    color: var(--front-mark);
    font-size: 46px;
  }
  .card-back { background: var(--card); }
  .wave { position: absolute; inset: 0; }
  .slogan {
    position: absolute;
    right: 30px;
    top: 82px;
    color: var(--text-light);
    font-size: 14px;
    line-height: 1.4;
    text-align: right;
  }
  .back-brand {
    position: absolute;
    left: 40px;
    top: 120px;
  }
  .card-back .brand-name {
    color: var(--green);
    font-size: 34px;
    text-align: left;
  }
  .follow {
    position: absolute;
    left: 40px;
    top: 232px;
    display: flex;
    align-items: center;
    gap: 8px;
    color: var(--blue);
    font-size: 14px;
  }
  .social-dot {
    width: 22px; height: 22px;
    border-radius: 50%;
    background: var(--blue);
  }
  .social-dot + .social-dot { background: var(--green); }
  .contact-block {
    position: absolute;
    right: 32px;
    bottom: 20px;
    text-align: right;
  }
  .person-name {
    color: var(--blue);
    font-size: 24px;
    font-weight: 600;
    text-transform: uppercase;
    letter-spacing: 1px;
    line-height: 1.2;
  }
  .credentials {
    color: var(--text-muted);
    font-size: 13px;
    margin-bottom: 8px;
  }
  .contact-line {
    display: flex;
    justify-content: flex-end;
    align-items: center;
    gap: 10px;
    color: var(--text-light);
    font-size: 15px;
    line-height: 1.5;
  }
  .contact-line svg { width: 14px; height: 14px; fill: none; stroke: var(--green); stroke-width: 2; }
</style>
</head>
<body>
  <section class="card card-front">
    <div class="brand-name">Varden<br>Therapy</div>
  </section>

  <section class="card card-back">
    <svg class="wave" viewBox="0 0 620 354" aria-hidden="true">
      <path d="M60 0 H620 V178 C530 176 470 150 420 104 C350 40 240 8 60 0 Z" fill="var(--blue)"/>
      <path d="M40 20 C230 26 350 72 405 124 C455 172 530 190 620 192 V202 C520 200 440 184 392 134 C340 86 220 38 40 32 Z" fill="var(--green)"/>
    </svg>

    <p class="slogan">Mobile Physiotherapy<br>Your Road To Recovery</p>

    <div class="back-brand">
      <div class="brand-name">Varden<br>Therapy</div>
    </div>

    <div class="follow">
      <span>Follow us on:</span>
      <span class="social-dot"></span>
      <span class="social-dot"></span>
    </div>

    <div class="contact-block">
      <div class="person-name">Luke Varden</div>
      <div class="credentials">BSc(kin), MPT, CAFCI, IMS</div>
      <div class="contact-line">867-555-0142
        <svg viewBox="0 0 24 24"><path d="M5 3h4l2 5-3 2a11 11 0 0 0 6 6l2-3 5 2v4a2 2 0 0 1-2 2A17 17 0 0 1 3 5a2 2 0 0 1 2-2z"/></svg>
      </div>
      <div class="contact-line">VardenTherapy@postnest.ca
        <svg viewBox="0 0 24 24"><rect x="3" y="5" width="18" height="14" rx="1"/><path d="M3 6l9 7 9-7"/></svg>
      </div>
      <div class="contact-line">www.VardenTherapy.ca
        <svg viewBox="0 0 24 24"><circle cx="12" cy="12" r="9"/><path d="M3 12h18M12 3c3 3 3 15 0 18M12 3c-3 3-3 15 0 18"/></svg>
      </div>
    </div>
  </section>
</body>
</html>
```